Printing company needs postcard design targeting restaurants

8.5" x 11" card touting printing & mailing services of interest to restaurants. Rough copy attached. Feel free to edit. Needs mail panel. Must conform to post office regulations. Must provide hi res PDF & editable native doc. with all fonts & links.

Printing

```html
<!DOCTYPE html>
<html lang="en">
<head>
<meta charset="utf-8">
<title>Restaurant Printing Postcard</title>
<link rel="stylesheet" href="https://fonts.googleapis.com/css2?family=Bebas+Neue&family=Lato:wght@400;700&family=Oswald:wght@500&display=swap">
<style>
  :root {
    --lime: #9cc43a;
    --lime-light: #c6e25a;
    --slate: #3f3f45;
    --slate-dark: #2f2f33;
    --ink: #1d1d1f;
    --paper: #ffffff;
    --backdrop: #e9e7e3;
    --text-light: #f4f4f4;
  }
  * { box-sizing: border-box; margin: 0; padding: 0; }
  html, body { width: 806px; height: 1200px; overflow: hidden; }
  body { background: var(--backdrop); font-family: 'Lato', sans-serif; position: relative; }

  .card { position: absolute; left: 28px; width: 750px; height: 560px; overflow: hidden; box-shadow: 0 2px 8px rgba(0,0,0,.18); }
  .card--front { top: 22px; background: var(--slate); }
  .card--back { top: 618px; background: var(--paper); }
  .card svg.shapes { position: absolute; inset: 0; }

  .tile { position: absolute; border: 6px solid var(--lime); background: var(--paper); padding: 6px; }
  .tile .art { width: 100%; height: 100%; }
  .tile--menu { left: 0; top: 0; width: 206px; height: 158px; }
  .tile--menu .art { background: linear-gradient(160deg, #f6d9a6, #e89a4c 55%, #5d8b3a); }
  .tile--board { left: 214px; top: 0; width: 160px; height: 160px; border-color: var(--paper); }
  .tile--board .art { background: linear-gradient(180deg, #fafafa, #e2e2e2); }
  .tile--loyalty { left: 0; top: 166px; width: 232px; height: 188px; }
  .tile--loyalty .art { background: linear-gradient(135deg, #f5a623, #e0352a); border: 14px solid var(--paper); }
  .tile--reserved { left: 242px; top: 172px; width: 196px; height: 176px; border-color: var(--paper); padding: 0; }
  .tile--reserved .art { background: linear-gradient(160deg, #7b4a2e, #caa57b 60%, #eadcc7); }
  .tile--wine { left: 0; top: 362px; width: 284px; height: 198px; border-color: var(--slate-dark); padding: 0; }
  .tile--wine .art { background: linear-gradient(160deg, #3a1c22, #121214); }
  .tile--glasses { left: 294px; top: 362px; width: 230px; height: 198px; border-color: var(--paper); padding: 0; }
  .tile--glasses .art { background: linear-gradient(170deg, #d9dde0, #8c9399 60%, #4b5056); }

  .heading { font-family: 'Bebas Neue', sans-serif; font-weight: 400; line-height: 1; display: flex; align-items: center; gap: 10px; }
  .heading::after { content: ""; flex: 1; height: 1px; background: currentColor; opacity: .7; }

  .front-text { position: absolute; color: var(--text-light); font-size: 11.4px; line-height: 1.32; }
  .heading--tents { position: absolute; left: 414px; top: 14px; width: 320px; font-size: 34px; color: var(--lime-light); }
  .copy--tents { left: 416px; top: 56px; width: 318px; }
  .heading--tips { position: absolute; left: 380px; top: 192px; width: 358px; font-size: 33px; color: var(--lime-light); }
  .copy--tips { left: 500px; top: 240px; width: 242px; text-align: center; }
  .promo-strip { position: absolute; left: 432px; top: 350px; width: 318px; height: 30px; padding: 2px 8px 0 10px; font-size: 6.6px; line-height: 1.25; font-weight: 700; color: var(--ink); }
  .heading--menus { position: absolute; left: 540px; top: 410px; font-family: 'Oswald', sans-serif; font-weight: 500; font-size: 14.5px; color: var(--lime-light); }
  .copy--menus { left: 556px; top: 434px; width: 184px; }

  .eddm { position: absolute; left: 44px; top: 432px; width: 440px; font-size: 14.6px; line-height: 1.26; color: var(--slate-dark); }

  .back-col { position: absolute; left: 18px; top: 16px; width: 272px; color: var(--ink); }
  .back-col .heading { font-size: 29px; margin-bottom: 3px; }
  .back-col .heading::after { max-width: 110px; }
  .back-col p { font-size: 9.6px; line-height: 1.28; margin-bottom: 3px; }
  .back-col section { margin-bottom: 6px; }

  .stamp { position: absolute; left: 618px; top: 56px; width: 86px; height: 112px; border: 1.5px solid #333; }
  .address-line { position: absolute; left: 436px; width: 300px; height: 1px; background: #555; }

  .audience { position: absolute; left: 312px; top: 450px; width: 430px; color: var(--text-light); }
  .audience h3 { font-family: 'Oswald', sans-serif; font-weight: 500; font-size: 10.5px; line-height: 1.25; color: var(--lime-light); text-transform: uppercase; margin-bottom: 8px; }
  .audience ul { list-style: none; display: grid; grid-template-columns: 95px 108px 115px 100px; row-gap: 2px; font-family: 'Oswald', sans-serif; font-size: 12px; grid-auto-flow: column; grid-template-rows: repeat(3, auto); }
  .audience li::before { content: "\2192"; color: var(--lime-light); margin-right: 4px; }
</style>
</head>
<body>

<article class="card card--front">
  <div class="tile tile--menu"><div class="art" role="img" aria-label="Illustrated restaurant menu card with a countryside scene"></div></div>
  <div class="tile tile--board"><div class="art" role="img" aria-label="Chalkboard table tent reading dish of the day"></div></div>
  <div class="tile tile--loyalty"><div class="art" role="img" aria-label="Orange plastic loyalty card"></div></div>
  <div class="tile tile--reserved"><div class="art" role="img" aria-label="Reserved sign on a set restaurant table"></div></div>
  <div class="tile tile--wine"><div class="art" role="img" aria-label="Wine house promotional sign"></div></div>
  <div class="tile tile--glasses"><div class="art" role="img" aria-label="Glassware on a restaurant table"></div></div>

  <svg class="shapes" width="750" height="560" viewBox="0 0 750 560" aria-hidden="true">
    <defs>
      <linearGradient id="bannerFill" x1="0" y1="0" x2="1" y2="0">
        <stop offset="0" stop-color="#9cc43a"/>
        <stop offset="1" stop-color="#c6e25a"/>
      </linearGradient>
    </defs>
    <polygon points="380,0 750,0 750,560 524,560" fill="var(--slate)"/>
    <polygon points="374,0 382,0 526,560 518,560" fill="var(--paper)"/>
    <polygon points="348,186 750,186 750,228 360,228" fill="var(--slate)" stroke="var(--paper)" stroke-width="2"/>
    <polygon points="420,229 444,229 500,348 476,348" fill="var(--lime)"/>
    <polygon points="432,350 750,350 750,380 432,380" fill="var(--lime)"/>
    <polygon points="520,388 750,388 750,400 523,400" fill="var(--slate-dark)"/>
    <polygon points="30,420 505,416 552,532 30,544" fill="url(#bannerFill)"/>
  </svg>

  <h2 class="heading heading--tents">Table Tents</h2>
  <p class="front-text copy--tents">Table tent printing puts your message in front of a receptive audience and lets you advertise at the point of sale. We offer tent cards in multiple sizes and shapes, including 4" x 6", 4.25" x 6", 4" x 8," and 5" x 5.5" vertical and 7" x 5" horizontal. Our table tents are printed on sturdy ultra-thick cardstock and are simple to set up.</p>

  <h2 class="heading heading--tips">Marketing Tips</h2>
  <p class="front-text copy--tips">With competition for consumer dollars fierce, many businesses are adopting new strategies to appeal to customers. Food and beverage establishments are among those that are constantly refining their operations in an effort to strengthen their appeal to the public and sell more to each paying customer.</p>

  <p class="promo-strip">We offer full-color outside printing on tent cards so you can achieve maximum impact with your promotion. Choose a glossy or matte finish to match your branding and style. Our prices are competitive and we offer easy and convenient ordering. Small orders welcome!</p>

  <h2 class="heading--menus">WATERPROOF/WASHABLE MENUS</h2>
  <p class="front-text copy--menus">The Waterproof Menu is custom printed on a Waterproof Synthetic Paper created to withstand the harsh, every day restaurant elements. We offer several manufacturing options including: Spiral Bound Menus, Bi-Fold or Tri-Fold Menus, and Single</p>

  <p class="eddm">Every Route Mailer is a program developed by the Postal Service to enable your business to send postcards or advertisements to a target audience without the need to purchase a mailing list or print specific addresses on your mail piece.</p>
</article>

<article class="card card--back">
  <svg class="shapes" width="750" height="560" viewBox="0 0 750 560" aria-hidden="true">
    <polygon points="0,0 318,0 272,560 0,560" fill="var(--lime)"/>
    <polygon points="318,0 342,0 298,560 272,560" fill="var(--ink)"/>
    <polygon points="306,420 750,420 750,560 296,560" fill="var(--ink)"/>
  </svg>

  <div class="back-col">
    <section>
      <h2 class="heading">Banners</h2>
      <p>All restaurants, regardless of their cuisine, should employ vinyl restaurant banners to help brand their name and convey the style of dining they offer.<br>Regardless of your area, restaurants have to advertise to compete with each other to attract the lunch crowd during day time hours and the dinner crowd at night. With a different advertisement for each, restaurants can easily create colorful banners to reflect their daily and nightly specials to help engage families and business people as they dine-out. Promoting your restaurant properly to attract the locals can be the determining factor to how successful your restaurant becomes.</p>
    </section>
    <section>
      <h2 class="heading">Signs</h2>
      <p>Using signs to advertise your Restaurant is a key element in your overall marketing strategy to engage your target audience and find new customers wanting to dine with you. Restaurants often cater to impulse marketing to attract new patrons, and impulse driven messages can be created to attract Walk-in customers from foot traffic and patrons who drive near you.</p>
    </section>
    <section>
      <h2 class="heading">Loyatly Cards</h2>
      <p>Custom printed plastic loyalty &amp; rewards cards are a great way to attract repeat business and reward your most loyal customers.</p>
      <p>In addition to increased sales revenue, loyalty &amp; rewards cards have proven to be an invaluable marketing tool, when coupled with POS software. If you are already offering gift cards to your customers, your POS system likely has a loyalty &amp; rewards program, too! Looking to upgrade your current loyalty or rewards program? Consider a loyalty key tag or card + key tag combo!</p>
    </section>
  </div>

  <div class="stamp" aria-label="Postage area"></div>
  <div class="address-line" style="top:186px"></div>
  <div class="address-line" style="top:222px"></div>
  <div class="address-line" style="top:258px"></div>

  <div class="audience">
    <h3>Many types of food and beverage service businesses can benefit from table<br>tent printing, including:</h3>
    <ul>
      <li>Bars</li><li>Restaurants</li><li>Lounges</li>
      <li>Grills</li><li>Gourmet stores</li><li>Food trucks</li>
      <li>Coffee shops</li><li>Eating events</li><li>Gastropubs</li>
      <li>Cafeterias</li><li>Nightclubs</li><li>Steakhouses</li>
    </ul>
  </div>
</article>

</body>
</html>
```